Automotive eCommerce Business looking for a business card design

Looking for a clean and simple business card design. Our company name is "Brindle Auto" and we are a company specializing in the ecommerce sales of automotive parts, specifically for pick up trucks and large SUVs. Our company colours are red, black, and white.

Feel free to use the logo provided or create a new logo that you seem fit. Looking forward to your creative ideas!

Industry/Entity Type

Automotive

Contact Information for Business Card

We were thinking of a possibly two-sided design featuring just the logo and company name on one side, and personal information on the other side. Single sided designs will be considered as well.

Font styles to use
Serif
Sans Serif
Decorative

Colors
ec1f27
ffffff
000000

Requirements
Must have
• Space for employee's name, title, phone number and email address, along with the company address and website somewhere.

```html
<!DOCTYPE html>
<html lang="en">
<head>
<meta charset="utf-8">
<title>Brindle Auto Ltd. — Business Card</title>
<link rel="stylesheet" href="https://fonts.googleapis.com/css2?family=Cinzel:wght@400;600&family=Roboto:wght@400;500&family=Roboto+Condensed:wght@500;700&display=swap">
<style>
  :root {
    --backdrop: #262626;
    --card-white: #f6f6f6;
    --brand-red: #a31e22;
    --ink-grey: #4a4a4a;
    --ink-light: #ffffff;
  }
  * { margin: 0; padding: 0; box-sizing: border-box; }
  html, body { width: 1200px; height: 960px; overflow: hidden; }
  body { background: var(--backdrop); position: relative; font-family: "Roboto", sans-serif; }

  .card {
    position: absolute;
    left: 320px;
    width: 600px;
    height: 342px;
    border-radius: 16px;
    overflow: hidden;
    background: var(--card-white);
  }
  .card--front { top: 105px; }
  .card--back { top: 493px; }

  /* Front side */
  .brand {
    position: absolute;
    top: 156px;
    left: 0;
    width: 100%;
    display: flex;
    justify-content: center;
    align-items: center;
    gap: 14px;
  }
  .brand__dot {
    width: 22px;
    height: 22px;
    background: var(--brand-red);
    border-radius: 50%;
  }
  .brand__name {
    font-family: "Cinzel", serif;
    font-weight: 600;
    font-size: 30px;
    color: var(--ink-grey);
    letter-spacing: 0.5px;
  }
  .front__web {
    position: absolute;
    top: 294px;
    width: 100%;
    text-align: center;
    font-size: 14px;
    letter-spacing: 5px;
    color: var(--ink-grey);
  }

  /* Back side */
  .back__panel { position: absolute; inset: 0; }
  .person {
    position: absolute;
    left: 34px;
    top: 30px;
    color: var(--ink-light);
    font-family: "Roboto Condensed", sans-serif;
  }
  .person__name { font-size: 21px; font-weight: 700; line-height: 1.2; }
  .person__title { font-size: 15px; font-weight: 500; }
  .address {
    position: absolute;
    left: 34px;
    top: 170px;
    color: var(--ink-light);
    font-size: 14px;
    line-height: 18px;
  }
  .contacts {
    position: absolute;
    left: 34px;
    top: 218px;
    list-style: none;
    color: var(--ink-light);
    font-size: 14px;
    line-height: 19.2px;
  }
  .contacts li { display: flex; align-items: center; gap: 8px; }
  .contacts svg { width: 14px; height: 14px; fill: var(--ink-light); flex: none; }
</style>
</head>
<body>

<section class="card card--front" aria-label="Card front">
  <div class="brand">
    <span class="brand__dot"></span>
    <span class="brand__name">Brindle Auto Ltd.</span>
  </div>
  <p class="front__web">www.brindleauto.com</p>
</section>

<section class="card card--back" aria-label="Card back">
  <svg class="back__panel" viewBox="0 0 600 342" preserveAspectRatio="none" aria-hidden="true">
    <polygon points="0,0 470,0 600,95 600,245 530,342 0,342" fill="var(--brand-red)"/>
  </svg>

  <div class="person">
    <p class="person__name">MARK ELLISON</p>
    <p class="person__title">CEO/FOUNDER</p>
  </div>

  <p class="address">4120 Larkspur Road<br>Fairbanks, Alaska 99701</p>

  <ul class="contacts">
    <li>
      <svg viewBox="0 0 16 16"><path d="M3.6 1.2l2.3 2.6-1.2 1.9c.9 2 2.4 3.5 4.4 4.5l1.9-1.2 2.6 2.3-1.3 2.4C7.4 13.4 2.6 8.6 1.2 3.3z"/></svg>
      <span>555 214 7730</span>
    </li>
    <li>
      <svg viewBox="0 0 16 16"><path d="M4.5 1h7v14h-7zM6 2.5v9.5h4V2.5zM7.3 13h1.4v1H7.3z" fill-rule="evenodd"/></svg>
      <span>555 381 0462</span>
    </li>
    <li>
      <svg viewBox="0 0 16 16"><path d="M4 1h8v4H4zM1 6h14v6h-3v3H4v-3H1zM5 10v4h6v-4z" fill-rule="evenodd"/></svg>
      <span>555 907 6158</span>
    </li>
    <li>
      <svg viewBox="0 0 16 16"><path d="M1 3.5h14v9H1zM2 4.5l6 4.5 6-4.5v-.2H2z"/></svg>
      <span>mark@brindleauto.com</span>
    </li>
    <li>
      <svg viewBox="0 0 16 16"><circle cx="8" cy="8" r="6.5"/><path d="M5 4c1.5.5 2 2 1 3s1 2 2 3-1 3 0 3" stroke="var(--brand-red)" stroke-width="1.4" fill="none"/></svg>
      <span>www.brindleauto.com</span>
    </li>
  </ul>
</section>

</body>
</html>
```